Water ATM Card

Need a design for water ATM cards. Size of card is 3.375 x 2.125 inch
On the Front include the Cedar hollow Logo.
Bottom right corner should have Price $100
On the Back
This card is to be used to access water refills at any Cedar Hollow Water Vending Machines.
Please contact (869) 418 2930 or (869) 534 1276 or email clearflowbox@mailvista.example for any assistance or recharging of card.

```html
<!DOCTYPE html>
<html lang="en">
<head>
<meta charset="utf-8">
<title>Cedar Hollow Water Card</title>
<link href="https://fonts.googleapis.com/css2?family=Poppins:ital,wght@0,400;0,600;0,700;1,700&display=swap" rel="stylesheet">
<style>
  :root {
    --page-bg: #e9e9e9;
    --card-white: #ffffff;
    --deep-blue: #28489a;
    --sky-blue: #1e92d2;
    --wave-navy: #2b3990;
    --wave-mid: #2a7cc6;
    --brand-blue: #1a6fbd;
    --green-dark: #1f9b45;
    --green-light: #86c440;
    --text-light: #ffffff;
  }
  html, body {
    margin: 0;
    padding: 0;
    width: 1093px;
    height: 1200px;
    overflow: hidden;
    background: var(--page-bg);
    font-family: "Poppins", sans-serif;
  }
  .canvas {
    position: relative;
    width: 1093px;
    height: 1200px;
  }
  .card {
    position: absolute;
    left: 259px;
    width: 578px;
    height: 356px;
    border-radius: 24px;
    overflow: hidden;
  }
  .card-front { top: 226px; background: var(--card-white); }
  .card-back {
    top: 621px;
    background: linear-gradient(90deg, var(--deep-blue), var(--sky-blue));
  }
  .back-top-band {
    position: absolute;
    top: 0;
    left: 0;
    right: 0;
    height: 120px;
    background: linear-gradient(90deg, var(--green-dark), var(--green-light));
  }
  .front-blue-band {
    position: absolute;
    left: 0;
    right: 0;
    top: 250px;
    bottom: 0;
    background: linear-gradient(90deg, var(--deep-blue), var(--sky-blue));
  }
  .wave-placeholder {
    position: absolute;
    left: 0;
    right: 0;
    background: linear-gradient(90deg, var(--wave-navy), var(--wave-mid));
  }
  .card-front .wave-placeholder { top: 178px; height: 72px; }
  .card-back .wave-placeholder { top: 110px; height: 86px; }
  .brand-name {
    position: absolute;
    top: 92px;
    left: 0;
    right: 0;
    margin: 0;
    text-align: center;
    font-weight: 700;
    font-size: 28px;
    line-height: 40px;
    letter-spacing: 0.5px;
    color: var(--brand-blue);
  }
  .price {
    position: absolute;
    right: 32px;
    top: 294px;
    margin: 0;
    font-weight: 600;
    font-size: 23px;
    line-height: 32px;
    color: var(--text-light);
  }
  .usage-note {
    position: absolute;
    top: 51px;
    left: 0;
    right: 0;
    margin: 0;
    text-align: center;
    font-weight: 600;
    font-size: 17px;
    line-height: 22px;
    text-transform: uppercase;
    color: var(--text-light);
  }
  .contact-line {
    position: absolute;
    left: 0;
    right: 0;
    margin: 0;
    text-align: center;
    color: var(--text-light);
  }
  .contact-lead { top: 210px; font-size: 17px; line-height: 24px; }
  .contact-phones { top: 232px; font-weight: 600; font-size: 24px; line-height: 30px; }
  .contact-phones .joiner { font-weight: 400; font-size: 16px; }
  .contact-or { top: 259px; font-size: 17px; line-height: 22px; }
  .contact-email { top: 280px; font-weight: 700; font-style: italic; font-size: 22px; line-height: 30px; }
  .contact-tail { top: 306px; font-size: 17px; line-height: 22px; }
</style>
</head>
<body>
<main class="canvas">

  <section class="card card-front" aria-label="Card front">
    <div class="front-blue-band"></div>
    <div class="wave-placeholder" role="img" aria-label="Decorative flowing water wave in blue tones"></div>
    <p class="brand-name">CEDAR HOLLOW</p>
    <p class="price">PRICE $100</p>
  </section>

  <section class="card card-back" aria-label="Card back">
    <div class="back-top-band"></div>
    <div class="wave-placeholder" role="img" aria-label="Decorative flowing water wave in blue and green tones"></div>
    <p class="usage-note">This card is to be used to access water refills<br>at any Cedar Hollow water vending machines</p>
    <p class="contact-line contact-lead">Please contact</p>
    <p class="contact-line contact-phones">(869) 418 2930 <span class="joiner">or</span> (869) 534 1276</p>
    <p class="contact-line contact-or">or</p>
    <p class="contact-line contact-email">clearflowbox@mailvista.example</p>
    <p class="contact-line contact-tail">for any assistance or recharging of card</p>
  </section>

</main>
</body>
</html>
```